THE WELLNESS BARN WEBSITE for Physio, Fitness, health

An attractive website advertising a physiotherapyand fitness / gym business, not generic, colours are natural, greens, browns, beiges. No cheesy pictures. With the ability to sell a small,amount of goods online if i decide to. Simple to navigate. Text boxes that i can input the main information and change easily. Somewhere to put my timetable. Easy to find contact details. However many pages it needs, im not fussed.
Target Market(s)
People looking for rehabilitation or fitness classes
Industry/Entity Type
Physiotherapy, Fitness, Gym, Health
Coding
Coded - Design and coding required
Number of Pages Required
1 page
Font styles to use
Other font styles liked:
- Im not fusse,ld, not script
Requirements
Must have
- Will upload posts from my business insta page for reference about the feel. Earthy natural tones, I have a lot of timber, and rustic looking piece's, plants etc in my clinic
Nice to have
- Simple to navigate
Should not have
- Cheesy "yoga" or generic "people doing physio" pics

```html
<!DOCTYPE html>
<html lang="en">
<head>
<meta charset="utf-8">
<title>The Wellness Barn Coral Bay</title>
<link href="https://fonts.googleapis.com/css2?family=Poppins:wght@400;500;600;700;800&display=swap" rel="stylesheet">
<style>
:root{
  --green:#26431c;
  --green-deep:#1f3816;
  --ink:#1c1c1c;
  --muted:#555;
  --pale:#eeeeee;
  --pill:#e6e9e2;
  --white:#fff;
  --star:#f0a020;
}
*{box-sizing:border-box;margin:0;padding:0}
html,body{width:1200px;height:4866px;overflow:hidden}
body{font-family:'Poppins',sans-serif;color:var(--ink);background:var(--white);position:relative}
.abs{position:absolute}

/* hero */
.hero{position:absolute;left:0;top:0;width:1200px;height:670px;background:linear-gradient(160deg,#5a4636 0%,#3a2e25 45%,#1e1914 100%)}
.nav{position:absolute;left:113px;top:21px;width:976px;height:104px;background:var(--white);border-radius:52px;display:flex;align-items:center;padding:0 28px;font-size:15px;font-weight:600;text-transform:uppercase}
.nav a{color:var(--ink);text-decoration:none;margin-right:32px}
.nav .active{background:var(--green);color:#fff;padding:7px 20px;border-radius:20px;margin-left:14px}
.nav .right{margin-left:auto;display:flex}
.nav .right a{margin:0 0 0 32px}
.nav .right a:last-child{margin-right:24px}
.brand{position:absolute;left:522px;top:0;width:156px;height:156px;border-radius:50%;background:var(--white);display:flex;align-items:center;justify-content:center;text-align:center;font-weight:800;font-size:17px;line-height:1.15;color:var(--green)}
.hero h1{position:absolute;top:236px;width:1200px;text-align:center;color:#fff;font-size:46px;font-weight:700;line-height:53px}
.hero p{position:absolute;top:358px;left:220px;width:760px;text-align:center;color:#fff;font-size:20px;font-weight:500;line-height:31px}
.hero .cta{position:absolute;left:520px;top:522px;width:160px;height:45px;border-radius:23px;background:var(--green);color:#fff;font-size:14px;font-weight:700;display:flex;align-items:center;justify-content:center}
.dots{position:absolute;left:1135px;top:318px}
.dots span{display:block;width:13px;height:13px;border:2px solid #fff;border-radius:50%;margin-bottom:11px}
.dots span.on{background:#fff}

h2.title{position:absolute;width:1200px;text-align:center;font-size:50px;font-weight:800;color:var(--green);letter-spacing:.5px}
.lead{position:absolute;text-align:center;font-size:16px;line-height:25px;color:var(--ink)}

/* services */
.svc{position:absolute;top:958px;width:318px;height:509px;background:#fff;border-radius:14px;box-shadow:0 6px 18px rgba(0,0,0,.12);overflow:hidden;text-align:center}
.svc .ph{height:240px}
.svc h3{font-size:20px;font-weight:600;line-height:30px;margin:18px 20px 10px}
.svc p{font-size:15px;line-height:24px;color:var(--muted);margin:0 24px}
.svc .btn{position:absolute;left:82px;bottom:28px;width:154px;height:44px;border-radius:22px;background:var(--pill);font-size:14px;font-weight:700;display:flex;align-items:center;justify-content:center}
.svc .btn.on{background:var(--green);color:#fff}
.sdots{position:absolute;top:1511px;left:582px;display:flex;gap:8px}
.sdots span{width:13px;height:13px;border-radius:50%;border:2px solid var(--green)}
.sdots span.on{background:var(--green)}

/* bands */
.band{position:absolute;left:0;width:1200px;background:var(--green)}

/* products */
.prod{position:absolute;top:1814px;width:231px;text-align:center;color:#fff}
.prod .ph{height:227px;border:3px solid #fff;border-radius:18px}
.prod p{font-size:17px;font-weight:600;line-height:26px;margin-top:18px}
.prod .plus{width:32px;height:32px;border:2px solid #fff;border-radius:50%;margin:12px auto 0;font-size:22px;line-height:27px;font-weight:500}

/* team */
.team{position:absolute;top:2500px;width:318px;height:441px;background:#fff;border-radius:14px;box-shadow:0 6px 18px rgba(0,0,0,.12);text-align:center}
.team.sel{border:2px solid #333;box-shadow:none}
.team .av{width:136px;height:136px;border-radius:50%;margin:32px auto 20px}
.team h3{font-size:21px;font-weight:600}
.team .role{font-size:15px;font-weight:700;color:var(--green);margin:6px 0 20px}
.team p{font-size:14.5px;line-height:24px;color:var(--muted);margin:0 26px}
.team .soc{display:flex;justify-content:center;gap:10px;margin-top:20px}
.team .soc span{width:30px;height:30px;border-radius:50%;background:var(--pill)}
.team .soc span.on{background:var(--green)}

/* faq */
.faq{position:absolute;left:166px;width:868px;background:#fff;border-radius:18px;box-shadow:0 4px 12px rgba(0,0,0,.08);padding:0 24px;font-size:15px}
.faq .q{display:flex;justify-content:space-between;align-items:center;height:55px}
.faq.open{border:2px solid #444;padding-bottom:12px}
.faq .a{font-size:14px;line-height:26px;color:var(--muted);margin-top:-6px;padding-right:120px}
.faq svg{width:20px;height:20px}
.fbtn{position:absolute;left:506px;top:3632px;width:188px;height:46px;border-radius:23px;background:var(--green);color:#fff;font-weight:700;font-size:15px;display:flex;align-items:center;justify-content:center}

/* testimonials */
.tst{position:absolute;top:4054px;width:306px;height:264px;background:#fff;border-radius:4px;text-align:center;padding-top:70px}
.tst .av{position:absolute;left:106px;top:-48px;width:94px;height:94px;border-radius:50%;border:4px solid #fff}
.tst h4{font-size:17px;font-weight:700;color:var(--green)}
.tst .tag{font-size:13px;font-weight:600;margin-top:2px}
.tst .stars{color:var(--star);font-size:13px;letter-spacing:2px;margin:6px 0 8px}
.tst p{font-size:14.5px;line-height:25px;margin:0 26px}
.arrow{position:absolute;top:4170px;width:34px;height:34px;border-radius:50%;display:flex;align-items:center;justify-content:center}

/* footer */
.fbrand{position:absolute;left:113px;top:4600px;width:172px;text-align:center;font-weight:800;font-size:30px;line-height:36px;color:var(--green)}
.fcol h5{font-size:16px;font-weight:700;color:var(--green);margin-bottom:16px}
.fcol ul{list-style:disc;padding-left:26px;font-size:14px;line-height:29px}
.crow{display:flex;align-items:center;gap:20px;font-size:14px;line-height:21px;margin-bottom:18px}
.crow .ic{width:36px;height:36px;border-radius:50%;background:var(--pill);display:flex;align-items:center;justify-content:center;flex:none}
.nl label{font-size:13px}
.nl .line{width:286px;border-bottom:1px solid #bbb;margin:6px 0 18px;height:14px}
.nl .sub{width:134px;height:46px;border-radius:23px;background:var(--green);color:#fff;font-weight:700;font-size:15px;display:flex;align-items:center;justify-content:center}
.bottom{position:absolute;left:113px;top:4802px;width:976px;border-top:1px solid #ccc}
.pay{position:absolute;top:4824px;display:flex;gap:4px}
.pay span{width:30px;height:18px;border-radius:2px}
.copy{position:absolute;top:4825px;left:0;width:1200px;text-align:center;font-size:12px;font-weight:500}
.fsoc{position:absolute;top:4815px;left:1006px;display:flex;gap:10px}
.fsoc span{width:36px;height:36px;border-radius:50%;border:2px solid var(--green)}
.fsoc span.on{background:var(--green)}
</style>
</head>
<body>

<section class="hero">
  <div role="img" aria-label="Photo of a woman lifting a barbell in a gym" style="position:absolute;inset:0"></div>
  <nav class="nav">
    <a class="active">Home</a><a>About Us</a><a>Our Services</a>
    <div class="right"><a>Products</a><a>FAQ</a><a>Contact Us</a></div>
  </nav>
  <div class="brand">THE<br>WELLNESS<br>BARN</div>
  <h1>THE WELLNESS BARN<br>CORAL BAY</h1>
  <p>Discover a healthier you with our Physiotherapist led programs. At The Wellness Barn Coral Bay, we focus on safe and effective movement to enhance your quality of life.<br><span style="display:block;margin-top:10px">Join us for a comprehensive approach to wellbeing.</span></p>
  <div class="cta">GET STARTED</div>
  <div class="dots"><span></span><span class="on"></span><span></span><span></span></div>
</section>

<h2 class="title" style="top:760px">OUR SERVICES</h2>
<p class="lead" style="left:125px;width:950px;top:843px">The Wellness Barn Coral Bay is dedicated to empowering individuals to achieve their health and wellbeing goals through safe and effective movement. Our core values include Integrity, Collaboration, Inclusivity, and a strong Commitment to health. We believe in providing professional support tailored to each individual's needs.</p>

<div class="svc" style="left:98px"><div class="ph" role="img" aria-label="Photo of a group exercise class for older adults" style="background:linear-gradient(135deg,#c9c6bd,#8a8f86)"></div><h3>Physiotherapy Classes<br>for Everyone</h3><p>Our classes are tailored for all ages, focusing on safe movement to enhance mobility and overall health.</p><div class="btn">LEARN MORE</div></div>
<div class="svc" style="left:440px"><div class="ph" role="img" aria-label="Photo of a staff member in a branded shirt in the gym" style="background:linear-gradient(135deg,#6f6f6c,#2d2d2b)"></div><h3>Holistic Wellness<br>Programs</h3><p>Our programs integrate physical activity with nutritional guidance to support sustainable health improvements.</p><div class="btn on">LEARN MORE</div></div>
<div class="svc" style="left:782px"><div class="ph" role="img" aria-label="Photo of people training with medicine balls" style="background:linear-gradient(135deg,#8c7f72,#4c443d)"></div><h3>Mindfulness and Yoga<br>Sessions</h3><p>Join our yoga sessions to improve mental clarity and physical flexibility in a calming environment.</p><div class="btn">LEARN MORE</div></div>
<div class="sdots"><span class="on"></span><span></span></div>

<section class="band products" style="top:1610px;height:630px"></section>
<h2 class="title" style="top:1714px;color:#fff">OUR PRODUCTS</h2>
<div class="prod" style="left:112px"><div class="ph" role="img" aria-label="Product photo of a spray bottle beside a plant" style="background:linear-gradient(135deg,#4f6a3a,#2a3a22)"></div><p>Lorem ipsum dolor sit amet consea</p><div class="plus">+</div></div>
<div class="prod" style="left:359px"><div class="ph" role="img" aria-label="Product photo of a cap and t-shirt" style="background:linear-gradient(135deg,#b9b8b2,#5c6150)"></div><p>Lorem ipsum dolor sit amet consea</p><div class="plus">+</div></div>
<div class="prod" style="left:608px"><div class="ph" role="img" aria-label="Product photo of a wheat heat bag and gift box" style="background:linear-gradient(135deg,#c9b49a,#a3643e)"></div><p>Lorem ipsum dolor sit amet consea</p><div class="plus" style="background:#fff;color:var(--green)">+</div></div>
<div class="prod" style="left:856px"><div class="ph" role="img" aria-label="Product photo of cups among dried flowers" style="background:linear-gradient(135deg,#b8a57c,#7b4d5a)"></div><p>Lorem ipsum dolor sit amet consea</p><div class="plus">+</div></div>

<h2 class="title" style="top:2368px">GET TO KNOW US</h2>
<p class="lead" style="left:0;width:1200px;top:2443px;font-size:17px">Discover the dedicated professionals committed to your health.</p>
<div class="team" style="left:98px"><div class="av" role="img" aria-label="Portrait of the lead physiotherapist" style="background:linear-gradient(135deg,#e4dcd2,#9a8677)"></div><h3>Dr. Hannah Rowe</h3><div class="role">Lead Physiotherapist</div><p>Dr. Hannah specializes in sports rehabilitation and has over 10 years of experience in helping clients recover from injuries.</p><div class="soc"><span></span><span></span></div></div>
<div class="team sel" style="left:440px"><div class="av" role="img" aria-label="Portrait of the wellness coach" style="background:linear-gradient(135deg,#6a5848,#2f2620)"></div><h3>Liam Foster</h3><div class="role">Wellness Coach</div><p>Liam focuses on holistic health and wellness, guiding clients through lifestyle changes to improve their overall wellbeing.</p><div class="soc"><span class="on"></span><span></span></div></div>
<div class="team" style="left:782px"><div class="av" role="img" aria-label="Portrait of the physiotherapy assistant" style="background:linear-gradient(135deg,#5f7fa0,#2c3a4a)"></div><h3>Mia Tran</h3><div class="role">Physiotherapy Assistant</div><p>Mia assists in physiotherapy sessions and is passionate about helping clients achieve their health goals.</p><div class="soc"><span></span><span></span></div></div>

<section class="band faq-band" style="top:3030px;height:715px;background:var(--pale)"></section>
<h2 class="title" style="top:3172px">FAQ</h2>
<p class="lead" style="left:190px;width:820px;top:3250px;font-size:17px;line-height:26px">Find answers to common questions about our health and wellness programs, services, and how we can support your journey to better health.</p>
<div class="faq" style="top:3338px"><div class="q">What types of programs do you offer?<svg viewBox="0 0 20 20"><circle cx="10" cy="10" r="10" fill="#1c1c1c"/><path d="M8 5l5 5-5 5" stroke="#fff" stroke-width="2" fill="none"/></svg></div></div>
<div class="faq open" style="top:3408px"><div class="q">How can I get started?<svg viewBox="0 0 20 20"><circle cx="10" cy="10" r="9" fill="none" stroke="#1c1c1c" stroke-width="2"/><path d="M5.5 8l4.5 4.5L14.5 8" stroke="#1c1c1c" stroke-width="2" fill="none"/></svg></div><p class="a">Getting started is easy! Simply contact us through our website or visit our location to discuss your health goals and find the right program for you.</p></div>
<div class="faq" style="top:3536px;height:52px"><div class="q" style="height:52px">Are your classes suitable for beginners?<svg viewBox="0 0 20 20"><circle cx="10" cy="10" r="10" fill="#1c1c1c"/><path d="M8 5l5 5-5 5" stroke="#fff" stroke-width="2" fill="none"/></svg></div></div>
<div class="fbtn">VIEW PROGRAMS</div>

<section class="band testimonials" style="top:3745px;height:725px"></section>
<h2 class="title" style="top:3872px;color:#fff">TESTIMONIALS</h2>
<p class="lead" style="left:0;width:1200px;top:3947px;font-size:17px;color:#fff">Hear from our clients about their transformative journeys with us.</p>
<div class="arrow" style="left:43px;background:var(--green-deep)"><svg width="14" height="14" viewBox="0 0 14 14"><path d="M9 2L4 7l5 5" stroke="#fff" stroke-width="2" fill="none"/></svg></div>
<div class="arrow" style="left:1122px;background:#fff"><svg width="14" height="14" viewBox="0 0 14 14"><path d="M5 2l5 5-5 5" stroke="#1c1c1c" stroke-width="2" fill="none"/></svg></div>
<div class="tst" style="left:112px"><div class="av" role="img" aria-label="Client portrait" style="background:linear-gradient(135deg,#d8b893,#7a5a40)"></div><h4>— CLAIRE BENNETT</h4><div class="tag">Fitness Enthusiast</div><div class="stars">★★★★★</div><p>The Wellness Barn has completely changed my approach to fitness. Their programs are tailored and effective!</p></div>
<div class="tst" style="left:448px"><div class="av" role="img" aria-label="Client portrait" style="background:linear-gradient(135deg,#d8b893,#7a5a40)"></div><h4>— CLAIRE BENNETT</h4><div class="tag">Fitness Enthusiast</div><div class="stars">★★★★★</div><p>The Wellness Barn has completely changed my approach to fitness. Their programs are tailored and effective!</p></div>
<div class="tst" style="left:782px"><div class="av" role="img" aria-label="Client portrait" style="background:linear-gradient(135deg,#d8b893,#7a5a40)"></div><h4>— CLAIRE BENNETT</h4><div class="tag">Fitness Enthusiast</div><div class="stars">★★★★★</div><p>The Wellness Barn has completely changed my approach to fitness. Their programs are tailored and effective!</p></div>

<footer>
  <div class="fbrand">THE<br>WELLNESS<br>BARN</div>
  <div class="fcol abs" style="left:323px;top:4548px"><h5>NAVIGATION</h5><ul><li>Home</li><li>About Us</li><li>Our Services</li><li>Products</li><li>FAQ</li><li>Contact Us</li><li>Privacy Policy</li></ul></div>
  <div class="fcol abs" style="left:484px;top:4548px"><h5>CONTACT US</h5>
    <div class="crow"><span class="ic"><svg width="14" height="18" viewBox="0 0 14 18"><path d="M7 0a7 7 0 0 0-7 7c0 5 7 11 7 11s7-6 7-11a7 7 0 0 0-7-7z" fill="#555"/><circle cx="7" cy="7" r="2.5" fill="#e6e9e2"/></svg></span>12/48 Ridge Hollow Rd<br>Kelsford, QLD 4600</div>
    <div class="crow"><span class="ic"><svg width="16" height="12" viewBox="0 0 16 12"><rect width="16" height="12" rx="1" fill="#555"/><path d="M0 1l8 6 8-6" stroke="#e6e9e2" stroke-width="1.5" fill="none"/></svg></span>hello@wellnessbarn.example</div>
    <div class="crow"><span class="ic"><svg width="16" height="16" viewBox="0 0 16 16"><path d="M3 1l3 3-2 2c1 2 3 4 5 5l2-2 3 3-2 3C7 15 1 9 1 3z" fill="#555"/></svg></span>040-555-0192</div>
  </div>
  <div class="fcol nl abs" style="left:801px;top:4548px"><h5>SIGN UP TO OUR NEWSLETTER</h5><label>Email</label><div class="line"></div><div class="sub">SUBSCRIBE</div></div>
  <div class="bottom"></div>
  <div class="pay" style="left:113px"><span style="background:#d7dde8"></span><span style="background:#c9d0e6"></span><span style="background:#e8c9b8"></span><span style="background:#b8cde6"></span><span style="background:#e6dccb"></span></div>
  <div class="copy">2025 © ALL RIGHTS RESERVED - THE WELLNESS BARN CORAL BAY</div>
  <div class="fsoc"><span class="on"></span><span></span></div>
</footer>

</body>
</html>
```